Help our Sugar Loom find our winning design! We're looking for a business card....

We’re a Sugar Loom in NY specializing in custom-made cakes and unique desserts.
Our cakes combine flavor and art, each designed to match customer’s special event and theme.
We’d like a unique business card with a clean design that will combine French chic and artistic look & feel.
We’d like to differentiate ourselves from standard bakeries, please don’t offer cupcake images :-)
Our logo is peach-pink and brown and we’d love to use these colors ( . Another color that can be added is gold - or feel free to suggest!

Target Market(s)

Women, ages 25-55

Industry/Entity Type

Boutique

Contact Information for Business Card

Text on card:
Logo
Sugar Loom by Dana Welch

www.sugarloomsweets.com
hello@sugarloom.com
(516) 555-0147
F – sugarloomnyc
IG - sugarloom_ny

Font styles to use
Sans Serif
Script

Requirements
Must have
• Logo
• Clean look
• French chic and artistic look & feel.
Nice to have
• Damask pattern
Should not have
• Cupcake images

```html
<!DOCTYPE html>
<html lang="en">
<head>
<meta charset="utf-8">
<title>Sugar Loom – Business Card</title>
<link href="https://fonts.googleapis.com/css2?family=Exo+2:wght@300;400;500&display=swap" rel="stylesheet">
<style>
  :root {
    --page: #e8e5e2;
    --card: #ffffff;
    --slate: #6a6765;
    --blush: #f28ea2;
    --blush-soft: #fbe3e8;
    --ink: #4a4644;
    --on-slate: #ffffff;
  }
  * { margin: 0; padding: 0; box-sizing: border-box; }
  html, body {
    width: 1200px;
    height: 900px;
    overflow: hidden;
    background: var(--page);
    font-family: "Exo 2", sans-serif;
  }
  .canvas {
    position: relative;
    width: 1200px;
    height: 900px;
  }
  .card {
    position: absolute;
    top: 200px;
    width: 500px;
    height: 500px;
    border-radius: 64px;
    background: var(--card);
    overflow: hidden;
    box-shadow: 0 10px 30px rgba(0,0,0,0.12);
  }
  .card--front { left: 70px; }
  .card--back { left: 630px; }
  .card__bands {
    position: absolute;
    inset: 0;
    width: 500px;
    height: 500px;
  }
  .contact-panel {
    position: absolute;
    left: 38px;
    top: 56px;
    color: var(--on-slate);
  }
  .contact-panel__name {
    font-size: 21px;
    font-weight: 500;
    letter-spacing: 1px;
    text-transform: uppercase;
  }
  .contact-panel__role {
    font-size: 14px;
    font-weight: 300;
    margin-top: 2px;
  }
  .contact-panel__address {
    margin-top: 42px;
    font-size: 13px;
    font-weight: 300;
    line-height: 1.45;
  }
  .contact-list {
    list-style: none;
    margin-top: 36px;
    font-size: 12.5px;
    font-weight: 300;
  }
  .contact-list__item {
    display: flex;
    align-items: center;
    gap: 8px;
    height: 24px;
  }
  .contact-list__icon {
    width: 12px;
    height: 12px;
    flex: none;
  }
  .brand {
    position: absolute;
    display: flex;
    align-items: center;
    justify-content: center;
  }
  .brand--front { left: 255px; top: 185px; width: 220px; height: 130px; }
  .brand--back { left: 110px; top: 170px; width: 280px; height: 160px; }
  .brand__ornament {
    position: absolute;
    inset: 0;
    border-radius: 50%;
    background: radial-gradient(ellipse at center, var(--blush-soft) 0%, rgba(251,227,232,0) 72%);
  }
  .brand__name {
    position: relative;
    font-size: 26px;
    font-weight: 400;
    color: var(--ink);
    letter-spacing: 0.5px;
  }
  .brand--back .brand__name { font-size: 32px; }
</style>
</head>
<body>
<main class="canvas">

  <section class="card card--front" aria-label="Business card front">
    <svg class="card__bands" viewBox="0 0 500 500" aria-hidden="true">
      <path d="M0 0 H266 C252 190 240 340 230 500 H0 Z" fill="var(--blush)"/>
      <path d="M0 0 H252 C238 190 226 340 216 500 H0 Z" fill="var(--slate)"/>
    </svg>

    <div class="contact-panel">
      <p class="contact-panel__name">Dana Welch</p>
      <p class="contact-panel__role">Managing Director</p>
      <p class="contact-panel__address">214 Orchard Street<br>New York NY</p>
      <ul class="contact-list">
        <li class="contact-list__item">
          <svg class="contact-list__icon" viewBox="0 0 12 12"><path d="M2.5 1 L4.5 1 L5.2 3.6 L4 4.6 C4.6 6 5.9 7.3 7.4 8 L8.4 6.8 L11 7.5 L11 9.5 C11 10.3 10.3 11 9.5 11 C5 11 1 7 1 2.5 C1 1.7 1.7 1 2.5 1 Z" fill="var(--on-slate)"/></svg>
          (516) 555-0147
        </li>
        <li class="contact-list__item">
          <svg class="contact-list__icon" viewBox="0 0 12 12"><rect x="3" y="0.5" width="6" height="11" rx="1.2" fill="none" stroke="var(--on-slate)"/><circle cx="6" cy="9.6" r="0.7" fill="var(--on-slate)"/></svg>
          F – sugarloomnyc
        </li>
        <li class="contact-list__item">
          <svg class="contact-list__icon" viewBox="0 0 12 12"><rect x="1" y="4" width="10" height="6" rx="1" fill="var(--on-slate)"/><rect x="3" y="1" width="6" height="3" fill="none" stroke="var(--on-slate)"/></svg>
          IG – sugarloom_ny
        </li>
        <li class="contact-list__item">
          <svg class="contact-list__icon" viewBox="0 0 12 12"><rect x="0.5" y="2" width="11" height="8" rx="1" fill="none" stroke="var(--on-slate)"/><path d="M0.8 2.4 L6 6.5 L11.2 2.4" fill="none" stroke="var(--on-slate)"/></svg>
          hello@sugarloom.com
        </li>
        <li class="contact-list__item">
          <svg class="contact-list__icon" viewBox="0 0 12 12"><circle cx="6" cy="6" r="5.3" fill="none" stroke="var(--on-slate)"/><ellipse cx="6" cy="6" rx="2.3" ry="5.3" fill="none" stroke="var(--on-slate)"/><path d="M0.7 6 H11.3" stroke="var(--on-slate)"/></svg>
          www.sugarloomsweets.com
        </li>
      </ul>
    </div>

    <div class="brand brand--front">
      <div class="brand__ornament" role="img" aria-label="Decorative pink flourish frame around the brand name"></div>
      <p class="brand__name">Sugar Loom</p>
    </div>
  </section>

  <section class="card card--back" aria-label="Business card back">
    <div class="brand brand--back">
      <div class="brand__ornament" role="img" aria-label="Decorative pink flourish frame around the brand name"></div>
      <p class="brand__name">Sugar Loom</p>
    </div>
  </section>

</main>
</body>
</html>
```